Global (re)insurance broker needs a business card design

We need a classic business card for our company that is headquartered in SG, with offices in Malaysia and Dubai. We specialise in insurance and reinsurance broking and consultancy for our global clients.

```html
<!DOCTYPE html>
<html lang="en">
<head>
<meta charset="utf-8">
<title>Corvane business card</title>
<link href="https://fonts.googleapis.com/css2?family=Open+Sans:wght@400;600;700&display=swap" rel="stylesheet">
<style>
  :root {
    --backdrop: #232323;
    --card: #1f1f24;
    --card-back: #17171a;
    --pattern: #1c1c1f;
    --mint: #c5e3bf;
    --blue: #2a4aa3;
    --white: #f2f2f2;
  }
  * { box-sizing: border-box; margin: 0; padding: 0; }
  html, body {
    width: 1200px; height: 780px; overflow: hidden;
    background: var(--backdrop);
    font-family: "Open Sans", Arial, sans-serif;
  }
  .card {
    position: absolute; top: 236px;
    width: 540px; height: 309px;
    box-shadow: 0 10px 30px rgba(0,0,0,.5);
    overflow: hidden;
  }
  .card-back { left: 40px; background: var(--card-back); }
  .card-front { left: 620px; background: var(--card); }

  .wordmark-pattern {
    position: absolute; inset: 0;
    background: linear-gradient(135deg, var(--pattern), var(--card-back));
  }
  .brand-name {
    position: absolute;
    color: var(--mint);
    font-weight: 600;
    letter-spacing: 2px;
    line-height: 1;
    white-space: nowrap;
  }
  .card-back .brand-name {
    left: 0; right: 0; top: 118px;
    text-align: center; font-size: 64px;
  }
  .card-front .brand-name { left: 36px; top: 34px; font-size: 42px; }

  .name-bar {
    position: absolute; left: 506px; top: 54px;
    width: 18px; height: 58px; background: var(--mint);
  }
  .person {
    position: absolute; right: 44px; top: 76px; text-align: right;
    white-space: nowrap;
  }
  .person-name {
    font-size: 28px; font-weight: 700; line-height: 1;
    color: var(--blue);
  }
  .person-name .surname { color: var(--mint); }
  .person-title {
    font-size: 14px; color: var(--white); margin-top: 5px;
  }
  .divider {
    position: absolute; left: 120px; right: 40px; top: 150px;
    height: 1px; background: var(--white);
  }
  .contacts {
    position: absolute; right: 26px; top: 166px;
    list-style: none; text-align: right;
    color: var(--white); font-size: 14px; line-height: 22px;
  }
  .contacts li { display: flex; justify-content: flex-end; align-items: center; gap: 8px; white-space: nowrap; }
  .contacts svg { width: 13px; height: 13px; }
  .address {
    position: absolute; left: 40px; top: 230px;
    color: var(--white); font-size: 14px; line-height: 20px;
    font-style: normal; white-space: nowrap;
  }
  .edge-bands { position: absolute; left: 0; bottom: 0; width: 540px; height: 50px; }
</style>
</head>
<body>

<section class="card card-back">
  <div class="wordmark-pattern" role="img" aria-label="Embossed repeating company name pattern in dark tones"></div>
  <div class="brand-name">CORVANE</div>
</section>

<section class="card card-front">
  <div class="brand-name">CORVANE</div>

  <div class="name-bar"></div>
  <div class="person">
    <div class="person-name">Mei Lin <span class="surname">Goh</span></div>
    <div class="person-title">Chief Operating Officer</div>
  </div>

  <div class="divider"></div>

  <ul class="contacts">
    <li>+65 9000 1234
      <svg viewBox="0 0 14 14" aria-hidden="true"><rect x="3.5" y="1" width="7" height="12" rx="1.5" fill="none" stroke="var(--mint)" stroke-width="1.3"/></svg>
    </li>
    <li>www.corvane.com
      <svg viewBox="0 0 14 14" aria-hidden="true"><circle cx="7" cy="7" r="6" fill="var(--blue)"/><path d="M1 7h12M7 1c-3 3-3 9 0 12M7 1c3 3 3 9 0 12" stroke="var(--white)" stroke-width=".7" fill="none"/></svg>
    </li>
    <li>meilin@corvane.com
      <svg viewBox="0 0 14 14" aria-hidden="true"><rect x="1" y="3" width="12" height="9" fill="var(--mint)"/><path d="M1 3l6 5 6-5" stroke="var(--card)" stroke-width="1" fill="none"/></svg>
    </li>
  </ul>

  <address class="address">25 Harbour Street, Marina<br>Tower #08-04, Singapore 018900</address>

  <svg class="edge-bands" viewBox="0 0 540 50" aria-hidden="true">
    <polygon points="0,23 368,23 374,17 378,17 372,30 0,30" fill="var(--mint)"/>
    <polygon points="0,36 380,36 392,10 540,10 540,50 0,50" fill="var(--blue)"/>
  </svg>
</section>

</body>
</html>
```